KBT Business Cards

We require business cards for our business. We would like a matte black back to the card, with our logo centred in the middle. The front side of the card is open to design.

Target Market(s)

Clients looking for legal services (professional)

Industry/Entity Type

Legal

Contact Information for Business Card

Doran Kelbrath
Partner
Mobile: 0461 738 524
Email: doran@kbtlaw.co
Website: www.kbtlaw.co
Level 3, 118 Wendmore Street
Sydney NSW 2000

Font styles to use
Other font styles liked:
• Avenir

Colors
f04a50
ffffff
1b1b1b

Requirements
Must have
• Black back with logo included in the centre of the card.
• Our font is Avenir.

```html
<!DOCTYPE html>
<html lang="en">
<head>
<meta charset="utf-8">
<title>KBT Business Cards</title>
<link href="https://fonts.googleapis.com/css2?family=Roboto:wght@400;500;700&display=swap" rel="stylesheet">
<style>
  :root {
    --backdrop: #e9e4dd;
    --kraft-light: #d3b089;
    --kraft-mid: #bf9767;
    --kraft-dark: #a7804f;
    --ink: #111111;
    --matte-black: #1b1b1b;
    --paper-white: #ffffff;
  }
  * { margin: 0; padding: 0; box-sizing: border-box; }
  html, body {
    width: 1200px; height: 900px; overflow: hidden;
    background: var(--backdrop);
    font-family: "Roboto", Arial, sans-serif;
    color: var(--ink);
  }
  .canvas { position: relative; width: 1200px; height: 900px; }
  .card {
    position: absolute;
    width: 556px; height: 343px;
    box-shadow: 2px 3px 6px rgba(0, 0, 0, 0.25);
  }
  .card--front {
    left: 330px; top: 90px;
    background: radial-gradient(ellipse at 40% 15%, var(--kraft-light), var(--kraft-mid) 55%, var(--kraft-dark));
  }
  .card--back {
    left: 330px; top: 469px; width: 559px;
    background: var(--matte-black);
    color: var(--paper-white);
  }

  .contact {
    position: absolute; left: 0; right: 0; top: 89px;
    text-align: center; font-size: 16.5px; line-height: 20.5px;
  }
  .contact__name { font-size: 19px; font-weight: 700; line-height: 22px; letter-spacing: 0.3px; }
  .contact__role { font-size: 16px; line-height: 18px; }
  .contact__rule { width: 141px; height: 1px; background: var(--ink); margin: 4px auto 5px; }
  .contact__label { font-weight: 700; }
  .contact__address { line-height: 20px; }

  .brand {
    position: absolute; inset: 0;
    display: flex; align-items: center; justify-content: center;
  }
  .brand__mark { width: 96px; height: 96px; background: var(--paper-white); margin-right: 40px; }
  .brand__name {
    font-size: 31px; font-weight: 500; line-height: 33px; text-transform: uppercase;
  }
</style>
</head>
<body>
<main class="canvas">
  <section class="card card--front" aria-label="Card front">
    <div class="contact">
      <p class="contact__name">DORAN KELBRATH</p>
      <p class="contact__role">Partner</p>
      <div class="contact__rule"></div>
      <p><span class="contact__label">M:</span> 0461 738 524</p>
      <p><span class="contact__label">E:</span> doran@kbtlaw.co</p>
      <p><span class="contact__label">W:</span> www.kbtlaw.co</p>
      <div class="contact__rule"></div>
      <p class="contact__address">Level 3, 118 Wendmore<br>Street, Sydney NSW 2000</p>
    </div>
  </section>

  <section class="card card--back" aria-label="Card back">
    <div class="brand">
      <div class="brand__mark"></div>
      <p class="brand__name">Kelbrath<br>Brandt<br>Legal</p>
    </div>
  </section>
</main>
</body>
</html>
```